Bikes for Dreams - Website Redesign

Create a professional website for a nonprofit; BikesforDreams.org
Please see boatsforelders.org and www.pedalsforhopes.org for the concept I am after.
The webpage should have a fun feel and should match the style of the company at www.pedalsforhopes.org. The pages to include are 'Home', 'About us' and 'Get Started'
Thank you and good luck!
Reason: i would like to see more designs.

```html
<!DOCTYPE html>
<html lang="en">
<head>
<meta charset="utf-8">
<title>Bikes for Dreams</title>
<link href="https://fonts.googleapis.com/css2?family=Raleway:wght@400;500;600;700;800&display=swap" rel="stylesheet">
<style>
:root{
  --blue:#1f9fe2;
  --blue-deep:#1689cc;
  --blue-light:#2bb3f0;
  --navy:#1c4d88;
  --title-blue:#1d9be0;
  --orange:#fdb813;
  --orange-edge:#d4920a;
  --ink:#333;
  --muted:#444;
  --icon-grey:#666;
  --band:#f2f2f2;
  --footer:#333;
  --white:#fff;
}
*{box-sizing:border-box;margin:0;padding:0}
html,body{width:993px;height:1200px;overflow:hidden;background:var(--white)}
body{position:relative;font-family:'Raleway',sans-serif;color:var(--ink)}
.abs{position:absolute}
.topbar{left:0;top:0;width:993px;height:82px;background:var(--blue)}
.nav a{position:absolute;top:32px;color:var(--white);font-size:12.5px;font-weight:500;text-decoration:none}
.phone{left:653px;top:28px;display:flex;align-items:center;gap:12px;color:var(--white);font-weight:700;font-size:19px}
.btn{display:flex;align-items:center;justify-content:center;background:var(--orange);color:var(--white);font-weight:700;border-bottom:3px solid var(--orange-edge);letter-spacing:.3px}
.btn-top{left:837px;top:24px;width:94px;height:37px;font-size:13.5px}
.sidebar{left:10px;top:0;width:274px;height:619px;background:var(--blue);border-radius:0 0 6px 6px}
.brand{left:10px;top:24px;width:274px;display:flex;flex-direction:column;align-items:center;gap:10px}
.brand-dot{width:58px;height:58px;border-radius:50%;background:var(--white)}
.brand-name{color:var(--white);font-weight:700;font-size:17.5px;letter-spacing:.3px}
.brand-rule{left:10px;top:138px;width:274px;height:1px;background:rgba(255,255,255,.25)}
.form-head{left:26px;top:154px;width:247px;height:41px;background:var(--blue-deep);color:var(--white);font-weight:700;font-size:16.5px;display:flex;align-items:center;padding-left:18px}
.form-body{left:26px;top:195px;width:247px;height:407px;background:var(--blue-light)}
.label{left:44px;color:var(--white);font-weight:600;font-size:13.5px}
.field{left:43px;width:213px;height:30px;background:var(--white);font-size:10px;color:#444;display:flex;align-items:center;padding:0 10px;justify-content:space-between}
.btn-submit{left:43px;top:552px;width:213px;height:36px;font-size:13.5px}
.hero{left:284px;top:82px;width:709px;height:350px;background:linear-gradient(135deg,#fbfdfe 0%,#e3f4fb 50%,#b9e6f6 100%)}
.hero-h{left:309px;top:181px;font-size:29px;font-weight:800;color:var(--navy)}
.hero-sub{left:311px;top:218px;font-size:17.5px;font-weight:600;color:var(--ink)}
.btn-hero{left:311px;top:253px;width:95px;height:37px;font-size:13.5px}
.hero-art{left:536px;top:184px;width:457px;height:248px;background:linear-gradient(160deg,rgba(231,76,60,.15),rgba(231,76,60,.55) 60%,rgba(90,110,140,.35));border-radius:40px 40px 0 0}
.dots{left:313px;top:394px;display:flex;gap:5px}
.dots span{width:9px;height:9px;border-radius:50%;background:#666}
.dots span:first-child{background:var(--blue)}
.section-h{left:284px;top:457px;width:709px;text-align:center;font-weight:700;font-size:19px;color:var(--ink)}
.step{width:200px;text-align:center}
.step h3,.feature h3{color:var(--title-blue);font-weight:700;font-size:15.5px;margin-bottom:8px}
.step p,.feature p{font-size:11.5px;line-height:18px;color:var(--muted)}
.step svg{display:block;margin:0 auto 16px}
.band{left:0;top:678px;width:993px;height:396px;background:var(--band)}
.feature{text-align:center}
.coin{width:50px;height:50px;border-radius:50%;background:var(--orange);margin:0 auto 25px;display:flex;align-items:center;justify-content:center}
.footer{left:0;top:1074px;width:993px;height:126px;background:var(--footer)}
.copy{left:0;top:1102px;width:993px;text-align:center;color:#bbb;font-size:11px;line-height:18px}
.social{left:420px;top:1150px;display:flex;gap:18px}
.social span{width:17px;height:17px;border-radius:50%;background:var(--white)}
</style>
</head>
<body>
<div class="abs topbar"></div>
<nav class="nav">
  <a style="left:282px">Home</a><a style="left:338px">About</a><a style="left:394px">How it Works</a><a style="left:490px">FAQ</a><a style="left:534px">Blog</a><a style="left:582px">Contact</a>
</nav>
<div class="abs phone">
  <svg width="16" height="16" viewBox="0 0 24 24"><path fill="#fff" d="M6.6 10.8a15 15 0 0 0 6.6 6.6l2.2-2.2c.3-.3.7-.4 1-.2 1.1.4 2.3.6 3.6.6.6 0 1 .4 1 1V20c0 .6-.4 1-1 1C10.6 21 3 13.4 3 4c0-.6.4-1 1-1h3.5c.6 0 1 .4 1 1 0 1.3.2 2.5.6 3.6.1.3 0 .7-.2 1z"/></svg>
  <span>1-800-555-0142</span>
</div>
<div class="abs btn btn-top">DONATE</div>

<div class="abs hero"></div>
<div class="abs hero-art" role="img" aria-label="Illustration of a cheerful family handing over keys beside a red car"></div>
<h1 class="abs hero-h">DONATE CAR TO CHARITY!</h1>
<p class="abs hero-sub">Your car can make a difference!</p>
<div class="abs btn btn-hero">DONATE</div>
<div class="abs dots"><span></span><span></span><span></span><span></span></div>

<aside>
  <div class="abs sidebar"></div>
  <div class="abs brand"><div class="brand-dot"></div><div class="brand-name">BIKES FOR DREAMS</div></div>
  <div class="abs brand-rule"></div>
  <div class="abs form-head">DONATION PICK UP FORM</div>
  <div class="abs form-body"></div>
  <div class="abs label" style="top:208px">Contact Information</div>
  <div class="abs field" style="top:234px">First Name:</div>
  <div class="abs field" style="top:270px">Last Name:</div>
  <div class="abs field" style="top:306px">Zip Code:</div>
  <div class="abs field" style="top:341px">&nbsp;Email Address:</div>
  <div class="abs field" style="top:376px">Day Phone</div>
  <div class="abs label" style="top:419px">Vehicle Donation Information</div>
  <div class="abs field" style="top:446px">Year of Vehicle:<span>&#8964;</span></div>
  <div class="abs field" style="top:481px">Make of Vehicle:<span>&#8964;</span></div>
  <div class="abs field" style="top:516px">Model of Vehicle<span>&#8964;</span></div>
  <div class="abs btn btn-submit">SUBMIT APPLICATION</div>
</aside>

<h2 class="abs section-h">HOW IT WORKS</h2>
<div class="abs step" style="left:303px;top:502px">
  <svg width="47" height="47" viewBox="0 0 47 47"><rect width="47" height="47" rx="6" fill="var(--icon-grey)"/><path fill="#fff" d="M15 11c2-1 4 0 5 2l2 4c.5 1.5 0 2.5-1 3.5l-1.5 1.2c1.5 3 3.5 5 6.5 6.5l1.2-1.5c1-1 2-1.5 3.5-1l4 2c2 1 3 3 2 5l-1 2c-1 2-3 3-5 2.6C20 35 12 27 10.4 17c-.4-2 .6-4 2.6-5z"/></svg>
  <h3>Call Us</h3><p>Lorem ipsum dolor sit<br>amet, consect..</p>
</div>
<div class="abs step" style="left:521px;top:500px">
  <svg width="72" height="50" viewBox="0 0 72 50"><g fill="var(--icon-grey)"><path d="M2 22h38V8h14l12 14v14H2z"/><path d="M6 2l18 16-3 2L4 5z"/><circle cx="14" cy="40" r="8"/><circle cx="56" cy="40" r="8"/></g><rect x="45" y="12" width="8" height="9" fill="#fff"/><circle cx="14" cy="40" r="3.5" fill="#fff"/><circle cx="56" cy="40" r="3.5" fill="#fff"/></svg>
  <h3>We Tow It</h3><p>Lorem ipsum dolor sit<br>amet, consect..</p>
</div>
<div class="abs step" style="left:735px;top:502px">
  <svg width="47" height="47" viewBox="0 0 47 47"><rect width="47" height="47" rx="6" fill="var(--icon-grey)"/><path fill="#fff" d="M29 10l8 8-16 16-9 2 2-9zM31 8l3-2 7 7-2 3z"/></svg>
  <h3>Tax Write Off</h3><p>Lorem ipsum dolor sit<br>amet, consect..</p>
</div>

<section>
  <div class="abs band"></div>
  <div class="abs feature" style="left:78px;top:723px;width:240px">
    <div class="coin"><svg width="30" height="22" viewBox="0 0 30 22"><g fill="#111"><path d="M1 10h16V3h6l6 7v6H1z"/><path d="M2 1l8 7-1.5 1L1 2.5z"/><circle cx="7" cy="18" r="3.5"/><circle cx="23" cy="18" r="3.5"/></g></svg></div>
    <h3>Free Local Towing</h3><p>Running or not, Any Condition &amp; Pickup<br>Anywhere.</p>
  </div>
  <div class="abs feature" style="left:375px;top:723px;width:240px">
    <div class="coin"><svg width="26" height="26" viewBox="0 0 26 26"><circle cx="13" cy="13" r="10" fill="none" stroke="#111" stroke-width="3"/><path d="M13 7v7h-4" fill="none" stroke="#111" stroke-width="2.5"/></svg></div>
    <h3>Fast Pickup</h3><p>Same Day to 24 Hours</p>
  </div>
  <div class="abs feature" style="left:648px;top:723px;width:290px">
    <div class="coin"><svg width="24" height="28" viewBox="0 0 24 28"><rect x="1" y="1" width="22" height="26" rx="2" fill="none" stroke="#111" stroke-width="2.5"/><rect x="5" y="5" width="14" height="5" fill="#111"/><g fill="#111"><rect x="5" y="13" width="3" height="3"/><rect x="10.5" y="13" width="3" height="3"/><rect x="16" y="13" width="3" height="3"/><rect x="5" y="18" width="3" height="3"/><rect x="10.5" y="18" width="3" height="3"/><rect x="16" y="18" width="3" height="3"/></g></svg></div>
    <h3>Income Tax Deduction</h3><p>We issue you an IRS tax receipt &amp; offer the<br>largest resale network to get you the highest tax<br>write-off possible.</p>
  </div>
  <div class="abs feature" style="left:219px;top:893px;width:260px">
    <div class="coin"><svg width="24" height="28" viewBox="0 0 24 28"><path d="M3 2h13l5 5v19H3z" fill="#111"/><g stroke="var(--orange)" stroke-width="1.6"><path d="M7 11h10M7 15h10M7 19h6"/></g></svg></div>
    <h3>No Paperwork Hassles</h3><p>We take any car and handle everything:<br>DMV, Smog, &amp; IRS paperwork.</p>
  </div>
  <div class="abs feature" style="left:496px;top:893px;width:300px">
    <div class="coin"><svg width="30" height="24" viewBox="0 0 30 24"><path d="M7 3h16l4 8h2v9h-4v3h-4v-3H9v3H5v-3H1v-9h2z" fill="#111"/><path d="M9 6h12l2.5 5h-17z" fill="var(--orange)"/><circle cx="7" cy="15" r="2" fill="var(--orange)"/><circle cx="23" cy="15" r="2" fill="var(--orange)"/></svg></div>
    <h3>Car donations help fund programs</h3><p>And benefit Bright Hope Youth Foundation<br>International. An IRS 501(c)3 nonprofit<br>organization.</p>
  </div>
</section>

<footer>
  <div class="abs footer"></div>
  <p class="abs copy">Copyright© 2017 Bright Hope Youth Foundation International<br>All Rights Reserved.</p>
  <div class="abs social"><span></span><span></span><span></span><span></span><span></span></div>
</footer>
</body>
</html>
```